Stationery & Envelope Design

Executive Style looking stationery & envelope design.
Business Information:
Brightfield Homes Group
2875 Birchwood Lane, Millbrook, OR 97402-4180
Phone: 541.555.0142
Fax: 541.555.0187

Industry/Entity Type

Business

```html
<!DOCTYPE html>
<html lang="en">
<head>
<meta charset="utf-8">
<title>Brightfield Homes Group – Stationery Set</title>
<link href="https://fonts.googleapis.com/css2?family=Arimo:wght@400;700&display=swap" rel="stylesheet">
<style>
  :root{
    --brand-blue:#0a4f9c;
    --brand-green:#76873a;
    --ink:#222;
    --rule:#333;
    --paper:#fff;
    --edge:#9a9a9a;
    --stage:#d9d4cc;
    --faint:#eeeeee;
  }
  *{box-sizing:border-box;margin:0;padding:0}
  html,body{width:1200px;height:1089px;overflow:hidden}
  body{background:var(--stage);font-family:"Arimo",Arial,sans-serif;color:var(--ink);position:relative}
  .sheet,.envelope{position:absolute;background:var(--paper);border:1px solid var(--edge);overflow:hidden}
  .corner{position:absolute;width:46px;height:46px}
  .corner.tl{left:0;top:0}
  .corner.tr{right:0;top:0;transform:scaleX(-1)}
  .corner.bl{left:0;bottom:0;transform:scaleY(-1)}
  .corner.br{right:0;bottom:0;transform:scale(-1,-1)}
  .brand-name{display:flex;align-items:center;gap:6px;font-weight:700;color:var(--brand-blue);white-space:nowrap;position:absolute;font-size:13px}
  .brand-name .mark{width:10px;height:10px;background:var(--brand-green)}
  .fax-sheet{left:87px;top:41px;width:473px;height:610px}
  .letterhead{left:649px;top:41px;width:473px;height:610px}
  .fax-sheet .brand-name{left:0;right:0;justify-content:center;top:50px}
  .contact-line{position:absolute;left:22px;top:80px;font-size:8px;white-space:nowrap}
  .contact-line .accent{color:var(--brand-green)}
  .contact-line b{color:var(--brand-blue);font-weight:400}
  .fax-title{position:absolute;left:33px;top:128px;font-size:29px;font-weight:400}
  .fax-fields{position:absolute;left:33px;top:181px;width:334px}
  .fax-row{display:flex;border-bottom:1.5px solid var(--rule);font-size:11px}
  .fax-row span{width:171px}
  .fax-row.r1{height:26px}
  .fax-row.r2{height:33px;padding-top:12px}
  .fax-row.r3{height:36px;padding-top:10px}
  .fax-row.r4{height:33px;padding-top:10px}
  .watermark{position:absolute;color:var(--faint);font-weight:700;text-align:center;white-space:nowrap}
  .fax-sheet .watermark{left:0;right:0;bottom:26px;font-size:13px}
  .letterhead .brand-name{left:42px;top:57px}
  .letterhead .address-block{position:absolute;left:309px;top:16px;font-size:8.5px;line-height:11px}
  .address-block .accent{color:var(--brand-green);font-size:9px}
  .address-block .gap{margin-top:3px;display:flex;align-items:center;gap:3px}
  .address-block svg{width:7px;height:7px}
  .letterhead .watermark{left:20px;right:20px;top:320px;font-size:28px}
  .flap{position:absolute;left:0;top:0;width:100%}
  .flap-name{position:absolute;left:0;right:0;display:flex;justify-content:center;align-items:center;gap:6px;font-weight:700;font-size:13px}
  .flap-name .mark{width:10px;height:10px}
  .env-white-a{left:85px;top:672px;width:527px;height:160px}
  .env-white-b{left:54px;top:751px;width:527px;height:160px}
  .env-front{left:48px;top:822px;width:529px;height:229px}
  .env-green{left:629px;top:672px;width:498px;height:232px}
  .env-blue{left:614px;top:739px;width:527px;height:230px}
  .env-black{left:603px;top:824px;width:530px;height:230px}
  .env-front .brand-name{left:28px;top:54px}
  .env-front .return-address{position:absolute;left:28px;top:83px;font-size:8px;line-height:11px}
  .return-address .accent{color:var(--brand-green)}
</style>
</head>
<body>

<svg width="0" height="0" style="position:absolute" aria-hidden="true">
  <defs>
    <path id="corner-art" d="M0 0 H46 A46 46 0 0 1 0 46 Z" fill="var(--brand-blue)"/>
  </defs>
</svg>

<section class="sheet fax-sheet">
  <svg class="corner tl" viewBox="0 0 46 46"><use href="#corner-art"/></svg>
  <svg class="corner tr" viewBox="0 0 46 46"><use href="#corner-art"/></svg>
  <svg class="corner bl" viewBox="0 0 46 46"><use href="#corner-art"/></svg>
  <svg class="corner br" viewBox="0 0 46 46"><use href="#corner-art"/></svg>
  <div class="brand-name"><span class="mark"></span>BRIGHTFIELD HOMES GROUP</div>
  <p class="contact-line"><span class="accent">Brightfield Homes Group,</span> 2875 Birchwood Lane, Millbrook, OR 97402-4180 | <b>P:</b> 541.555.0142 | <b>F:</b> 541.555.0187</p>
  <h1 class="fax-title">FAX</h1>
  <div class="fax-fields">
    <div class="fax-row r1"><span>To</span><span>From</span></div>
    <div class="fax-row r2"><span>Fax</span><span>Pages</span></div>
    <div class="fax-row r3"><span>Phone</span><span>Date</span></div>
    <div class="fax-row r4"><span>Re</span><span>CC</span></div>
  </div>
  <div class="watermark">BRIGHTFIELD HOMES GROUP</div>
</section>

<section class="sheet letterhead">
  <svg class="corner tl" viewBox="0 0 46 46"><use href="#corner-art"/></svg>
  <svg class="corner tr" viewBox="0 0 46 46"><use href="#corner-art"/></svg>
  <svg class="corner bl" viewBox="0 0 46 46"><use href="#corner-art"/></svg>
  <svg class="corner br" viewBox="0 0 46 46"><use href="#corner-art"/></svg>
  <div class="brand-name"><span class="mark"></span>BRIGHTFIELD HOMES GROUP</div>
  <div class="address-block">
    <div class="accent">Brightfield Homes Group</div>
    <div>2875 Birchwood Lane</div>
    <div>Millbrook, OR 97402-4180</div>
    <div class="gap"><svg viewBox="0 0 10 10"><path d="M2 1 L4 1 L5 3.5 L3.8 4.6 C4.5 6 5 6.5 6.4 7.2 L7.5 6 L9 7 L9 9 C5 9.5 0.5 5 2 1 Z" fill="var(--brand-green)"/></svg>541.555.0142</div>
    <div class="gap"><svg viewBox="0 0 10 10"><rect x="1" y="4" width="8" height="5" fill="var(--brand-green)"/><rect x="3" y="1" width="4" height="3" fill="var(--brand-green)"/></svg>541.555.0187</div>
  </div>
  <div class="watermark">BRIGHTFIELD HOMES GROUP</div>
</section>

<section class="envelope env-white-a">
  <svg class="flap" viewBox="0 0 527 70" height="70"><polyline points="0,1 30,68 497,68 527,1" fill="none" stroke="#bbb"/></svg>
  <div class="flap-name" style="top:30px;color:var(--brand-blue)"><span class="mark" style="background:var(--brand-green)"></span>BRIGHTFIELD HOMES GROUP</div>
</section>

<section class="envelope env-white-b">
  <svg class="flap" viewBox="0 0 527 70" height="70"><polyline points="0,1 30,68 497,68 527,1" fill="none" stroke="#bbb"/></svg>
  <div class="flap-name" style="top:25px;color:#444"><span class="mark" style="background:#444"></span>BRIGHTFIELD HOMES GROUP</div>
</section>

<section class="envelope env-front">
  <svg class="corner tl" viewBox="0 0 46 46"><use href="#corner-art"/></svg>
  <svg class="corner tr" viewBox="0 0 46 46"><use href="#corner-art"/></svg>
  <svg class="corner bl" viewBox="0 0 46 46"><use href="#corner-art"/></svg>
  <svg class="corner br" viewBox="0 0 46 46"><use href="#corner-art"/></svg>
  <div class="brand-name"><span class="mark"></span>BRIGHTFIELD HOMES GROUP</div>
  <div class="return-address">
    <div class="accent">Brightfield Homes Group</div>
    <div>2875 Birchwood Lane, Millbrook, OR 97402-4180</div>
  </div>
</section>

<section class="envelope env-green">
  <svg class="flap" viewBox="0 0 498 70" height="70"><polygon points="0,0 498,0 474,68 24,68" fill="var(--brand-green)"/></svg>
  <div class="flap-name" style="top:28px;color:#fff"><span class="mark" style="background:#fff"></span>BRIGHTFIELD HOMES GROUP</div>
</section>

<section class="envelope env-blue">
  <svg class="flap" viewBox="0 0 527 72" height="72"><polygon points="0,0 527,0 503,72 24,72" fill="var(--brand-blue)"/></svg>
  <div class="flap-name" style="top:29px;color:#fff"><span class="mark" style="background:#fff"></span>BRIGHTFIELD HOMES GROUP</div>
</section>

<section class="envelope env-black">
  <svg class="flap" viewBox="0 0 530 72" height="72"><polyline points="0,1 30,70 500,70 530,1" fill="none" stroke="#bbb"/></svg>
  <div class="flap-name" style="top:25px;color:#000"><span class="mark" style="background:#000"></span>BRIGHTFIELD HOMES GROUP</div>
</section>

</body>
</html>
```